New Business Cards for Tormin Group

We need a new Business Card to compliment our new logo. We are a vibrant design, manufacture and install business providing recreation areas, public parks and Municipal spaces. We want business cards that are classy, modern and clean.

We have recently changed our logo, and are celebrating our 40th anniversary. We want business cards with a new modern design to reflect our status.

Target Market(s)

Customers

Contact Information for Business Card

We need all the details of our 3 offices as per the business card attached. Please disregard the old logo on the business card, the other three files show our new logo.

Requirements
Must have
• All info as per attached business card but with new logo.
Nice to have

```html
<!DOCTYPE html>
<html lang="en">
<head>
<meta charset="utf-8">
<title>Tormin Group – Business Card</title>
<link rel="stylesheet" href="https://fonts.googleapis.com/css2?family=Roboto:wght@400;700;900&display=swap">
<style>
  :root {
    --brand-red: #e8343a;
    --map-red: #ee6a5c;
    --ink: #2b2b2b;
    --paper: #ffffff;
    --backdrop: #e9e9eb;
  }
  * { box-sizing: border-box; margin: 0; padding: 0; }
  html, body { width: 1200px; height: 800px; overflow: hidden; }
  body {
    background: var(--backdrop);
    font-family: "Roboto", Arial, sans-serif;
    color: var(--ink);
    display: flex;
    align-items: center;
    justify-content: center;
    gap: 40px;
  }
  .card {
    width: 550px;
    height: 314px;
    border-radius: 18px;
    position: relative;
    overflow: hidden;
    box-shadow: 0 6px 20px rgba(0,0,0,.15);
  }
  /* Front */
  .card-front { background: var(--brand-red); }
  .world-map {
    position: absolute;
    left: 60px; top: 34px;
    width: 440px; height: 240px;
    border-radius: 40% 45% 38% 42%;
    background: radial-gradient(ellipse at center, var(--map-red) 0%, rgba(238,106,92,.55) 60%, rgba(238,106,92,0) 100%);
  }
  .front-brand {
    position: absolute;
    left: 0; right: 0; top: 122px;
    display: flex; align-items: center; justify-content: center; gap: 12px;
    color: var(--paper);
  }
  .brand-dot {
    width: 44px; height: 44px; border-radius: 50%;
    border: 4px solid currentColor;
  }
  .brand-name {
    font-weight: 900; font-size: 38px; letter-spacing: 1px; text-transform: uppercase;
  }
  .front-web {
    position: absolute; left: 0; right: 0; top: 186px;
    text-align: center; color: var(--paper);
    font-size: 12px; letter-spacing: 3px;
  }
  /* Back */
  .card-back { background: var(--paper); }
  .offices {
    position: absolute; left: 28px; top: 26px; width: 250px;
  }
  .office { margin-bottom: 14px; }
  .office-title {
    font-weight: 700; font-style: italic; font-size: 14px;
    padding-bottom: 3px;
    border-bottom: 1.5px solid var(--brand-red);
    margin-bottom: 4px;
  }
  .office-line { font-size: 11px; line-height: 13px; }
  .contact {
    position: absolute; left: 310px; top: 26px; width: 215px;
  }
  .back-brand {
    display: flex; align-items: center; gap: 10px;
    color: var(--ink);
    padding-bottom: 10px;
    border-bottom: 1.5px solid var(--brand-red);
    margin-bottom: 46px;
  }
  .back-brand .brand-dot { width: 40px; height: 40px; border-color: var(--brand-red); }
  .back-brand .brand-name { font-size: 26px; }
  .person-name { font-weight: 700; font-size: 17px; }
  .person-title { color: var(--brand-red); font-size: 12px; margin-bottom: 8px; }
  .contact-row { display: flex; align-items: center; gap: 7px; font-size: 12px; line-height: 18px; }
  .contact-row svg { flex: none; }
  .back-web {
    margin-top: 10px; font-weight: 700; font-size: 13px; letter-spacing: 2.5px;
  }
  .back-web .accent { color: var(--brand-red); }
</style>
</head>
<body>
  <section class="card card-front" aria-label="Business card front">
    <div class="world-map" role="img" aria-label="Faint world map in light red behind the company name"></div>
    <div class="front-brand">
      <span class="brand-dot"></span>
      <span class="brand-name">Tormin Group</span>
    </div>
    <p class="front-web">www.torminworks.com</p>
  </section>

  <section class="card card-back" aria-label="Business card back">
    <div class="offices">
      <div class="office">
        <h3 class="office-title">Head Office</h3>
        <p class="office-line">P.O. Box: 31840 Abu Dhabi, U.A.E.</p>
        <p class="office-line">Tel No: +971 (0)2 5510372</p>
        <p class="office-line">Fax No: +971 (0)2 5510373</p>
        <p class="office-line">Email: sales@torminworks.com</p>
      </div>
      <div class="office">
        <h3 class="office-title">Dubai Office</h3>
        <p class="office-line">P.O. Box: 487210 Dubai, U.A.E.</p>
        <p class="office-line">Tel No: +971 (0)4 6623814</p>
        <p class="office-line">Fax No: +971 (0)4 6623815</p>
        <p class="office-line">Email: sales@torminworks.com</p>
      </div>
      <div class="office">
        <h3 class="office-title">Qatar Office</h3>
        <p class="office-line">P.O. Box: 20937 Doha, Qatar</p>
        <p class="office-line">Tel No: +974 40718352</p>
        <p class="office-line">Fax No: +974 40718353</p>
        <p class="office-line">Email: sales@torminworks.com</p>
      </div>
    </div>

    <div class="contact">
      <div class="back-brand">
        <span class="brand-dot"></span>
        <span class="brand-name">Tormin Group</span>
      </div>
      <p class="person-name">Samir Haddani</p>
      <p class="person-title">Managing Partner</p>
      <p class="contact-row">
        <svg width="14" height="14" viewBox="0 0 14 14" aria-hidden="true"><circle cx="7" cy="7" r="7" fill="#e8343a"/><rect x="4.5" y="3" width="5" height="8" rx="1" fill="none" stroke="#fff" stroke-width="1.2"/></svg>
        +971 (0)50 734 9068
      </p>
      <p class="contact-row">
        <svg width="14" height="14" viewBox="0 0 14 14" aria-hidden="true"><circle cx="7" cy="7" r="7" fill="#e8343a"/><rect x="3.5" y="4.5" width="7" height="5" fill="none" stroke="#fff" stroke-width="1.1"/><path d="M3.5 4.5 L7 7.5 L10.5 4.5" fill="none" stroke="#fff" stroke-width="1.1"/></svg>
        samir@torminworks.com
      </p>
      <p class="back-web">www.<span class="accent">torminworks</span>.com</p>
    </div>
  </section>
</body>
</html>
```